To promote our Catering Equipment services to our Laundry customers

Our company specialises in the supply, installation & maintenance of commercial laundry equipment, and we want a flyer that can be handed out to our laundry equipment customers to promote the fact that we also supply, rent, repair & service catering equipment as well (Catering equipment such as Cookers, Ovens etc)

Target Market(s)

The target market will be our existing customers. They trust us to repair their laundry equipment... why not trust us to do their catering equipment as well? Our customers are all business customers such as Care Homes for the elderly, Hotels etc.

Industry/Entity Type

Catering

Requirements
Must have
• Flyer will be approx. 216 x 139mm (To be confirmed) once we have a printer.
• It must include the www.brantleyservices-example.co.uk website address & our contact telephone number 0116 583 2901.
Nice to have
• Ideally it would pitch us a ' a one-stop shop' for all of their catering & laundry equipment needs.
• It might be better to be styled along a similar colour scheme as our website at www.brantleyservices-example.co.uk.

```html
<!DOCTYPE html>
<html lang="en">
<head>
<meta charset="utf-8">
<title>Brantley Services – Catering Equipment Flyer</title>
<link rel="stylesheet" href="https://fonts.googleapis.com/css2?family=Maven+Pro:wght@500;700&family=Questrial&display=swap">
<style>
  :root {
    --navy: #1c2a78;
    --navy-deep: #111a55;
    --blue: #2a3c9c;
    --red: #d9232d;
    --red-deep: #b81c26;
    --white: #ffffff;
    --paper: #f3f4f7;
  }
  * { box-sizing: border-box; margin: 0; padding: 0; }
  html, body { width: 875px; height: 1200px; overflow: hidden; background: var(--paper); }
  .flyer { position: relative; width: 875px; height: 1200px; overflow: hidden; background: var(--paper); font-family: "Questrial", sans-serif; }
  .flyer-bands { position: absolute; inset: 0; }

  .brand { position: absolute; left: 44px; top: 92px; display: flex; align-items: center; gap: 12px; }
  .brand-mark { width: 26px; height: 26px; background: var(--red); }
  .brand-name { font-family: "Maven Pro", sans-serif; font-weight: 700; font-size: 32px; color: var(--white); letter-spacing: 0.5px; }

  .contact { position: absolute; right: 40px; top: 30px; text-align: right; color: var(--white); }
  .contact-label { font-size: 19px; line-height: 22px; }
  .contact-phone { display: flex; align-items: center; justify-content: flex-end; gap: 10px; font-family: "Maven Pro", sans-serif; font-weight: 700; font-size: 34px; line-height: 40px; margin-top: 2px; }
  .contact-web { display: flex; align-items: center; justify-content: flex-end; gap: 7px; font-family: "Maven Pro", sans-serif; font-weight: 700; font-size: 17px; line-height: 22px; margin-top: 4px; }

  .hero-photo { position: absolute; left: 110px; top: 195px; width: 654px; height: 420px; border-radius: 260px 260px 300px 300px / 230px 230px 190px 190px; background: radial-gradient(ellipse at 60% 40%, #c9a77e 0%, #8a6a4c 45%, #2f3a55 100%); }

  .headline { position: absolute; left: 49px; top: 628px; width: 777px; height: 70px; border-radius: 35px; background: linear-gradient(180deg, var(--blue), var(--navy-deep)); color: var(--white); font-family: "Maven Pro", sans-serif; font-weight: 500; font-size: 35px; display: flex; align-items: center; padding-left: 25px; white-space: nowrap; }

  .body-copy { position: absolute; left: 50px; top: 718px; width: 770px; color: var(--white); font-size: 15px; line-height: 18px; text-align: justify; }
  .body-copy p + p { margin-top: 17px; }

  .product { position: absolute; }
  .product-dishwasher { left: 19px; top: 918px; width: 270px; height: 244px; background: linear-gradient(160deg, #d6d8dc, #8e9298); }
  .product-hob { left: 300px; top: 935px; width: 290px; height: 238px; border-radius: 50%; background: radial-gradient(circle, #3a3d42 0%, #8d9096 60%, #c7c9cd 100%); }
  .product-oven { left: 598px; top: 990px; width: 250px; height: 200px; background: linear-gradient(160deg, #cfd2d6, #6e7278); }
</style>
</head>
<body>
<main class="flyer">
  <svg class="flyer-bands" width="875" height="1200" viewBox="0 0 875 1200" aria-hidden="true">
    <defs>
      <linearGradient id="top-band" x1="0" y1="0" x2="1" y2="0">
        <stop offset="0" stop-color="#111a55"/>
        <stop offset="0.5" stop-color="#2a3c9c"/>
        <stop offset="1" stop-color="#1c2a78"/>
      </linearGradient>
      <linearGradient id="red-band" x1="0" y1="0" x2="0" y2="1">
        <stop offset="0" stop-color="#e02a33"/>
        <stop offset="1" stop-color="#b81c26"/>
      </linearGradient>
    </defs>
    <path d="M0 0 H875 V160 C700 215 520 205 380 180 C240 155 110 125 0 150 Z" fill="#d9232d"/>
    <path d="M0 0 H875 V150 C700 205 520 195 380 170 C240 145 110 115 0 135 Z" fill="url(#top-band)"/>
    <path d="M0 600 C150 550 300 570 450 605 C620 645 760 610 875 560 V890 C700 920 520 905 400 898 C250 890 100 900 0 935 Z" fill="url(#red-band)"/>
    <path d="M15 935 C150 900 320 888 460 893 C600 898 760 922 860 895 C770 930 640 925 470 910 C320 898 160 905 15 935 Z" fill="#2a3c9c"/>
    <path d="M0 1172 C200 1150 500 1150 875 1168 V1200 H0 Z" fill="#1c2a78"/>
  </svg>

  <header>
    <div class="brand">
      <span class="brand-mark"></span>
      <span class="brand-name">Brantley Services</span>
    </div>
    <div class="contact">
      <p class="contact-label">Call us on:</p>
      <p class="contact-phone">
        <svg width="30" height="30" viewBox="0 0 24 24" aria-hidden="true"><path fill="#ffffff" d="M6.6 10.8a15 15 0 0 0 6.6 6.6l2.2-2.2c.3-.3.7-.4 1-.2 1.1.4 2.3.6 3.6.6.6 0 1 .4 1 1V20c0 .6-.4 1-1 1A17 17 0 0 1 3 4c0-.6.4-1 1-1h3.5c.6 0 1 .4 1 1 0 1.3.2 2.5.6 3.6.1.3 0 .7-.2 1z"/></svg>
        0116 583 2901
      </p>
      <p class="contact-web">
        <svg width="18" height="18" viewBox="0 0 24 24" aria-hidden="true"><g fill="none" stroke="#7fb6ff" stroke-width="2"><circle cx="12" cy="12" r="10"/><path d="M2 12h20M12 2c3 3 3 17 0 20M12 2c-3 3-3 17 0 20"/></g></svg>
        www.brantleyservices-example.co.uk
      </p>
    </div>
  </header>

  <div class="hero-photo" role="img" aria-label="Engineer servicing a kitchen oven and replacing its filter"></div>

  <h1 class="headline">Catering Equipment Services in Your Area.</h1>

  <section class="body-copy">
    <p>All equipment supplied is backed by a team of engineers who are able to respond to your breakdowns quickly to minimise downtime. As well as breakdown repairs to your catering equipment, their engineers can provide preventative maintenance inspections and annual gas checks to ensure your legal and health &amp; safety compliance.</p>
    <p>The Catering equipment can be bought outright or rented/leased (to include free installation, annual servicing &amp; breakdown repairs). They can also offer maintenance cover for your existing machines. This ensures you have a ‘one-stop’ shop for all of your Catering equipment needs.</p>
  </section>

  <div class="product product-dishwasher" role="img" aria-label="Commercial stainless steel dishwasher with a rack of plates"></div>
  <div class="product product-hob" role="img" aria-label="Close view of a gas hob with cast iron pan supports"></div>
  <div class="product product-oven" role="img" aria-label="Commercial range cooker with open oven door"></div>
</main>
</body>
</html>
```